Business Card Design

I am a realtor and i also flip houses. I am CEO and Founder of my business which is Voskell Group LLC which is named after my great uncle who died and i was really close to. He was a wonderful friendly man so i want my business to represent him too. My business works with a lot of different people but i want mainly something to show i am a strong confidant woman who owns there own business. I have a really fun personality so i don't want anything TOO serious or manly. I want the perfect mix. My last two business cards i created are too embarrassing to hand out because they are far too girly and i deal with a lot of millionaire clients. I live out in the Palm Springs California area. I think its very important to show i am a single mom, female with her own business at only 24. I don't want to just be a female that blends in with all of the other serious people but yet i don't want to seem immature. People are telling me to stay away from pinks and purples but i don't want blues and greens because they represent men more. But i won't say no to them if there is a happy medium.

Industry/Entity Type

Realtor

Contact Information for Business Card

Voskell Group, LLC
Corinne Tabb
27358 Halvern Ave, C2 517
Marisol Vista, NV 89127
760-419-6735
Corinnedtabb@mailvane.com

```html
<!DOCTYPE html>
<html lang="en">
<head>
<meta charset="utf-8">
<title>Voskell Group LLC – Corinne Tabb</title>
<link rel="stylesheet" href="https://fonts.googleapis.com/css2?family=Aldrich&display=swap">
<style>
  :root {
    --peach: #fbbaa6;
    --rose: #c95a7d;
    --berry: #97205a;
    --plum: #74003d;
    --white: #ffffff;
    --teal: #167a80;
    --teal-dark: #0d5a5e;
  }
  html, body {
    margin: 0;
    padding: 0;
    width: 1200px;
    height: 702px;
    overflow: hidden;
    background: var(--white);
  }
  .card {
    position: relative;
    width: 1200px;
    height: 702px;
    overflow: hidden;
    background: linear-gradient(90deg, var(--peach) 0%, var(--rose) 35%, var(--berry) 65%, var(--plum) 100%);
    font-family: "Aldrich", sans-serif;
    font-weight: 400;
    color: var(--white);
  }
  .divider-dash {
    position: absolute;
    left: 426px;
    width: 22px;
    background: var(--white);
  }
  .base-rule {
    position: absolute;
    left: 0;
    top: 598px;
    width: 461px;
    height: 20px;
    background: var(--white);
  }
  .line {
    position: absolute;
    margin: 0;
    font-weight: 400;
    line-height: 1;
    white-space: nowrap;
  }
  .company { left: 494px; top: 130px; font-size: 46px; letter-spacing: 1px; }
  .person  { left: 499px; top: 228px; font-size: 42px; letter-spacing: 1px; }
  .address { left: 499px; font-size: 31px; }
  .address-1 { top: 308px; }
  .address-2 { top: 373px; }
  .address-3 { top: 437px; }
  .contact { font-size: 32px; }
  .phone   { left: 569px; top: 518px; }
  .email   { left: 584px; top: 588px; }
  .icon {
    position: absolute;
    fill: var(--teal);
  }
  .icon-phone { left: 511px; top: 512px; width: 42px; height: 42px; }
  .icon-mail  { left: 510px; top: 590px; width: 48px; height: 36px; }
</style>
</head>
<body>
  <div class="card">
    <div class="divider-dash" style="top:140px;height:50px"></div>
    <div class="divider-dash" style="top:228px;height:50px"></div>
    <div class="divider-dash" style="top:313px;height:51px"></div>
    <div class="divider-dash" style="top:398px;height:50px"></div>
    <div class="divider-dash" style="top:486px;height:52px"></div>
    <div class="base-rule"></div>

    <h1 class="line company">Voskell Group LLC</h1>
    <h2 class="line person">Corinne Tabb</h2>
    <p class="line address address-1">27358 Halvern Ave</p>
    <p class="line address address-2">C2 517 Marisol Vista</p>
    <p class="line address address-3">NV 89127</p>

    <svg class="icon icon-phone" viewBox="0 0 24 24" aria-hidden="true">
      <path d="M6.6 10.8c1.4 2.8 3.8 5.1 6.6 6.6l2.2-2.2c.3-.3.7-.4 1-.2 1.1.4 2.3.6 3.6.6.6 0 1 .4 1 1V20c0 .6-.4 1-1 1C10.6 21 3 13.4 3 4c0-.6.4-1 1-1h3.5c.6 0 1 .4 1 1 0 1.3.2 2.5.6 3.6.1.3 0 .7-.2 1l-2.3 2.2z"/>
    </svg>
    <p class="line contact phone">760-419-6735</p>

    <svg class="icon icon-mail" viewBox="0 0 48 36" aria-hidden="true">
      <path d="M0 0h48v36H0z"/>
      <path d="M1 1l23 19L47 1M1 35l17-17M47 35L30 18" fill="none" stroke="var(--teal-dark)" stroke-width="2"/>
    </svg>
    <p class="line contact email">corinnedtabb@mailvane.com</p>
  </div>
</body>
</html>
```